Kribbenisms, Brain-knotting short quips

I have over 500 statements or sayings that are very profound and consist of one line only. I call them Kribbenisms.
I am looking to publish these in 2022 in a book that will sell across the globe. The cover has to be eclectic, thought provoking and modern. I will also need designs, basic and simple if possible, for some of the inside pages.
Updates

It's New Year. need more time for designs

Target Market(s)

General audience 15 +

Requirements
Must have
• Originality.
Nice to have
• Originality. Abstract art
Should not have
• Copy and paste photographic designs.

```html
<!DOCTYPE html>
<html lang="en">
<head>
<meta charset="utf-8">
<title>Kribbenisms – Book Cover</title>
<link rel="stylesheet" href="https://fonts.googleapis.com/css2?family=Baloo+2:wght@800&family=Archivo+Black&display=swap">
<style>
  :root {
    --page-bg: #f4f4f4;
    --band-deep: #e8b2bf;
    --band-light: #f0ccd5;
    --motif-fill: #e6afbd;
    --motif-edge: #ffffff;
    --title-red: #e8103f;
    --subtitle-ink: #111111;
  }
  * { margin: 0; padding: 0; box-sizing: border-box; }
  html, body {
    width: 1200px; height: 864px; overflow: hidden;
    background: var(--page-bg);
  }
  .book-cover {
    position: absolute; left: 300px; top: 32px;
    width: 600px; height: 800px; overflow: hidden;
    background: repeating-linear-gradient(90deg,
      var(--band-deep) 0 100px, var(--band-light) 100px 200px);
    box-shadow: 0 6px 24px rgba(0,0,0,0.15);
  }
  .motif {
    position: absolute;
    background: var(--motif-fill);
    border: 5px solid var(--motif-edge);
    border-radius: 48% 48% 40% 40%;
  }
  .motif--centre { left: 140px; top: 260px; width: 330px; height: 300px; }
  .motif--top-corner { left: 440px; top: -90px; width: 220px; height: 160px; }
  .motif--bottom { left: 60px; top: 725px; width: 300px; height: 190px; }
  .title-block {
    position: absolute; left: 34px; top: 78px;
    width: 532px; text-align: center;
  }
  .book-title {
    font-family: "Baloo 2", sans-serif; font-weight: 800;
    font-size: 86px; line-height: 1; color: var(--title-red);
    letter-spacing: 1px; white-space: nowrap;
    text-shadow: 3px 0 0 #fff, -3px 0 0 #fff, 0 3px 0 #fff, 0 -3px 0 #fff,
                 2px 2px 0 #fff, -2px -2px 0 #fff, 2px -2px 0 #fff, -2px 2px 0 #fff;
  }
  .book-subtitle {
    font-family: "Archivo Black", sans-serif;
    font-size: 20px; color: var(--subtitle-ink);
    text-transform: uppercase; letter-spacing: 1px;
    white-space: nowrap; margin-top: 0;
  }
  .book-author {
    position: absolute; right: 34px; bottom: 112px;
    font-family: "Archivo Black", sans-serif;
    font-size: 26px; color: var(--title-red);
    text-transform: uppercase; letter-spacing: 1px;
    white-space: nowrap;
  }
</style>
</head>
<body>
  <main class="book-cover">
    <div class="motif motif--top-corner" role="img" aria-label="Outlined butterfly motif, partly cut off at the top edge"></div>
    <div class="motif motif--centre" role="img" aria-label="Large outlined pink butterfly illustration"></div>
    <div class="motif motif--bottom" role="img" aria-label="Outlined butterfly motif, partly cut off at the bottom edge"></div>
    <header class="title-block">
      <h1 class="book-title">Kribbenisms</h1>
      <p class="book-subtitle">Brain-knotting short quips</p>
    </header>
    <p class="book-author">Ivor Kribben</p>
  </main>
</body>
</html>
```